Trade Show Design

Two, doublesided backdrops/one doublesided banner/one countertop. I have 3 sample pictures of the 3 items that we are purchasing and all the dimensions are listed on the file names.
website: www.brickwisestudio.net
We are a training center that teaches homeowner's how to do their own home renovations through in-person classes with hands-on training.
We are looking to update our tradeshow displays utilizing stock photos as our photos do not have high enough resolution. I have attached lots of example pictures to select from but some of my favourites that I want to use are over 10 MB so they won't upload. Will have to figure out a different way to upload. Our tagline is Build your skills, room by room. We also use words such as "learn to reno" or "practical, hands-on training". We want to use our current branding (pictures of our minivan are uploaded as well) and our color palette document and really show people what we are all about - classes that people can attend so they can learn to reno their home.
Updates

For the 2 backdrops, we would like them to either be stand-alone or together incase we go to a trade show and only have room for 1 of them. They are to be different designs, front and back but a continuous flow if we are to use them together. Again, I have to figure out how to upload additional pictures as some of the ones I want to use are larger. Thanks!

Same with the Banner that is also double-sided - this is to be a different design for the back and front. We want minimal wording on everything but we really want to showcase what we do so that people can figure it out quickly when they walk by our booth....we offer in-person class with hands-on training. Learn to do by doing. Like on our vehicle that I sent example pictures of, we can put a list of a few topics so that people can understand:
Renovation Topics:
Bathroom
Drywall
Flooring
Tiling
Basement
Framing
Plumbing
Baseboards
Feature Walls

Here is the link to the Vornel Box to additional photos.

https://files.vornelbox.net/shared/7QK4r_mz2-TX8LwBnPe5YuJsdA0fGhRkZ?view=open

Thanks,
Marla

```html
<!DOCTYPE html>
<html lang="en">
<head>
<meta charset="utf-8">
<title>Brickwise Studio – Trade Show Displays</title>
<link rel="stylesheet" href="https://fonts.googleapis.com/css2?family=Oswald:wght@500;600;700&family=Nunito+Sans:wght@400;700;800&display=swap">
<style>
  :root{
    --teal:#2b6a74;
    --cream:#e8e6b3;
    --olive:#c9c596;
    --orange:#e0a23a;
    --sky:#b7d1ee;
    --blue:#5a86c2;
    --white:#ffffff;
    --stage:#dde4eb;
    --photo-warm:#b9a58c;
    --photo-cool:#9aa7b3;
    --photo-light:#d8cfc2;
  }
  *{box-sizing:border-box;margin:0;padding:0}
  html,body{width:1200px;height:511px;overflow:hidden}
  body{background:var(--stage);font-family:"Nunito Sans",Arial,sans-serif;position:relative}
  .piece{position:absolute;overflow:hidden}
  .cell{position:absolute;display:flex;flex-direction:column;align-items:center;justify-content:center;text-align:center}
  .photo{position:absolute}
  .photo.warm{background:linear-gradient(160deg,var(--photo-light),var(--photo-warm))}
  .photo.cool{background:linear-gradient(160deg,#c9d0d6,var(--photo-cool))}
  .teal{background:var(--teal)}
  .cream{background:var(--cream)}
  .orange{background:var(--orange)}
  .sky{background:var(--sky)}
  .topic{font-weight:800;font-size:8px;line-height:1.35;text-transform:uppercase}
  .topic.on-teal,.topic.on-orange{color:var(--white)}
  .topic.on-light{color:var(--teal)}
  .topic.small{font-size:5px}
  .icon{width:14px;height:14px;border-radius:3px;margin-bottom:6px}
  .icon.small{width:9px;height:9px;margin-bottom:3px}
  .icon.light{background:var(--white)}
  .icon.dark{background:var(--teal)}
  .icon.accent{background:var(--orange)}
  .brand{display:flex;flex-direction:column;align-items:center}
  .brand-name{font-weight:800;font-size:10px;color:var(--teal);display:flex;align-items:center;gap:4px;white-space:nowrap}
  .brand-mark{width:9px;height:9px;background:var(--orange)}
  .brand-tag{font-size:5.5px;color:var(--teal);margin-top:2px;white-space:nowrap}
  .brand.compact .brand-name{font-size:8px;gap:3px}
  .brand.compact .brand-mark{width:7px;height:7px}
  .brand.compact .brand-tag{font-size:4.5px}
  .headline{font-family:"Oswald",Impact,sans-serif;font-weight:600;line-height:.95}
  .url-pill{display:flex;align-items:center;gap:4px;background:var(--teal);color:var(--white);font-size:6.5px;border-radius:3px;padding:3px 6px 3px 3px;white-space:nowrap}
  .url-dot{width:10px;height:10px;border-radius:50%;background:var(--orange)}
  .underline{display:block}
</style>
</head>
<body>

<!-- Backdrop one: topic grid -->
<section class="piece backdrop backdrop-grid" style="left:20px;top:100px;width:370px;height:310px">
  <div class="photo warm" role="img" aria-label="Woman measuring wood with a pencil" style="left:0;top:0;width:92.5px;height:103px"></div>
  <div class="cell cream" style="left:92.5px;top:0;width:92.5px;height:103px">
    <div class="brand compact"><span class="brand-name"><span class="brand-mark"></span>Brickwise Studio</span><span class="brand-tag">Build your skills, room by room.</span></div>
  </div>
  <div class="photo cool" role="img" aria-label="Smiling woman using a hammer" style="left:185px;top:0;width:92.5px;height:103px"></div>
  <div class="cell orange" style="left:277.5px;top:0;width:92.5px;height:103px">
    <span class="icon light" role="img" aria-label="Drill icon"></span>
    <p class="topic on-orange">Drywall<br>Feature Walls<br>Framing</p>
  </div>

  <div class="cell cream" style="left:0;top:103px;width:92.5px;height:104px">
    <span class="icon dark" role="img" aria-label="Shower icon"></span>
    <p class="topic on-light">Tiling<br>Bathroom<br>Plumbing</p>
  </div>
  <div class="cell teal" style="left:92.5px;top:103px;width:185px;height:104px">
    <h1 class="headline" style="color:var(--white);font-size:34px">Learn<br>To Reno</h1>
    <svg class="underline" width="70" height="8" viewBox="0 0 70 8"><path d="M2 6 Q35 2 68 3" stroke="var(--orange)" stroke-width="1.2" fill="none"/></svg>
  </div>
  <div class="cell sky" style="left:277.5px;top:103px;width:92.5px;height:104px">
    <span class="icon dark" role="img" aria-label="Tool box icon"></span>
    <p class="topic on-light">Flooring<br>Baseboards<br>Basement</p>
  </div>

  <div class="photo warm" role="img" aria-label="Couple renovating a room with paint roller and tool belt" style="left:0;top:207px;width:128px;height:103px"></div>
  <div class="cell cream" style="left:128px;top:207px;width:112px;height:103px">
    <span class="url-pill"><span class="url-dot"></span>brickwisestudio.net</span>
  </div>
  <div class="photo cool" role="img" aria-label="Woman in safety glasses drilling wood" style="left:240px;top:207px;width:130px;height:103px"></div>
</section>

<!-- Backdrop two: practical training -->
<section class="piece backdrop backdrop-practical" style="left:405px;top:100px;width:370px;height:310px">
  <div class="cell" style="left:0;top:0;width:150px;height:310px;background:linear-gradient(180deg,var(--olive),#bcb887);justify-content:flex-start;padding-top:40px" role="img" aria-label="Tinted photo of a woman working on a renovation">
    <div class="brand"><span class="brand-name"><span class="brand-mark"></span>Brickwise Studio</span><span class="brand-tag">Build your skills, room by room.</span></div>
    <div style="margin-top:38px;display:flex;flex-direction:column;align-items:center">
      <span class="headline" style="color:var(--teal);font-size:27px">Practical.</span>
      <span class="headline" style="background:var(--orange);color:var(--white);font-size:21px;padding:2px 6px;margin:3px 0">Hands-on</span>
      <span class="headline" style="color:var(--teal);font-size:27px">Training.</span>
    </div>
    <div style="position:absolute;bottom:30px"><span class="url-pill"><span class="url-dot"></span>brickwisestudio.net</span></div>
  </div>
  <div class="cell teal" style="left:150px;top:0;width:110px;height:103px">
    <span class="icon light" role="img" aria-label="Drill icon"></span>
    <p class="topic on-teal">Drywall<br>Feature Walls<br>Framing</p>
  </div>
  <div class="cell cream" style="left:260px;top:0;width:110px;height:103px">
    <span class="icon dark" role="img" aria-label="Tool box icon"></span>
    <p class="topic on-light">Flooring<br>Baseboards<br>Basement</p>
  </div>
  <div class="photo warm" role="img" aria-label="Couple installing a ceiling light fixture" style="left:150px;top:103px;width:220px;height:104px"></div>
  <div class="photo cool" role="img" aria-label="Couple standing with tools and tool belts" style="left:150px;top:207px;width:110px;height:103px"></div>
  <div class="cell sky" style="left:260px;top:207px;width:110px;height:103px">
    <span class="icon dark" role="img" aria-label="Shower icon"></span>
    <p class="topic on-light">Tiling<br>Bathroom<br>Plumbing</p>
  </div>
</section>

<!-- Roll-up banner front -->
<section class="piece banner banner-front" style="left:848px;top:20px;width:140px;height:470px;background:var(--white)">
  <div class="photo cool" role="img" aria-label="Woman with cordless drill working on a wall" style="left:18px;top:8px;width:112px;height:125px"></div>
  <svg style="position:absolute;left:0;top:0" width="140" height="470" viewBox="0 0 140 470">
    <polygon points="22,133 130,100 130,112 40,140" fill="var(--orange)"/>
    <polygon points="20,138 36,133 36,148 20,150" fill="var(--sky)"/>
  </svg>
  <div class="photo warm" role="img" aria-label="Young woman holding two drills" style="left:40px;top:142px;width:65px;height:88px"></div>
  <div class="brand compact" style="position:absolute;left:0;right:0;top:245px">
    <span class="brand-name"><span class="brand-mark"></span>Brickwise Studio</span>
    <span class="brand-tag">Build your skills, room by room.</span>
  </div>
  <div style="position:absolute;left:12px;top:282px;width:10px;height:55px;background:var(--sky)"></div>
  <div style="position:absolute;left:12px;top:327px;width:40px;height:10px;background:var(--sky)"></div>
  <div style="position:absolute;left:24px;top:284px">
    <span class="headline" style="color:var(--teal);font-size:24px">Learn</span>
    <span class="headline" style="color:var(--orange);font-size:20px">To</span><br>
    <span class="headline" style="color:var(--orange);font-size:28px;margin-left:32px">Reno</span>
  </div>
  <svg style="position:absolute;left:58px;top:345px" width="60" height="6" viewBox="0 0 60 6"><path d="M2 4 Q30 1 58 3" stroke="var(--orange)" stroke-width="1" fill="none"/></svg>
  <div class="photo cool" role="img" aria-label="Couple posing with drill and tool belts" style="left:15px;top:362px;width:112px;height:108px"></div>
</section>

<!-- Roll-up banner back -->
<section class="piece banner banner-back" style="left:1025px;top:20px;width:140px;height:470px;background:var(--white)">
  <svg style="position:absolute;left:0;top:0" width="140" height="470" viewBox="0 0 140 470">
    <polygon points="105,0 140,0 140,40 105,25" fill="var(--cream)"/>
    <polygon points="0,255 12,255 12,300 0,300" fill="var(--sky)"/>
    <polygon points="20,340 140,305 140,320 20,345" fill="var(--cream)"/>
  </svg>
  <div class="brand compact" style="position:absolute;left:0;right:0;top:40px">
    <span class="brand-name"><span class="brand-mark"></span>Brickwise Studio</span>
    <span class="brand-tag">Build your skills, room by room.</span>
  </div>
  <div style="position:absolute;left:0;right:0;top:84px;display:flex;flex-direction:column;align-items:center">
    <span class="headline" style="color:var(--orange);font-size:11px">We Offer</span>
    <span class="headline" style="background:var(--teal);color:var(--white);font-size:15px;padding:2px 6px;margin:2px 0">IN-PERSON</span>
    <span class="headline" style="color:var(--blue);font-size:14px">CLASSES WITH</span>
    <span class="headline" style="color:var(--teal);font-size:12px">Hands-On Training</span>
  </div>
  <div class="cell" style="left:0;right:0;top:170px">
    <span class="icon small dark" role="img" aria-label="Shower icon"></span>
    <p class="topic small on-light">Tiling | Bathroom<br>Plumbing</p>
  </div>
  <div class="cell" style="left:0;right:0;top:208px">
    <span class="icon small accent" role="img" aria-label="Drill icon"></span>
    <p class="topic small" style="color:var(--orange)">Drywall | Framing<br>Feature Walls</p>
  </div>
  <div class="cell" style="left:0;right:0;top:246px">
    <span class="icon small dark" role="img" aria-label="Tool box icon"></span>
    <p class="topic small on-light">Flooring | Basement<br>Baseboards</p>
  </div>
  <div class="photo cool" role="img" aria-label="Man in glasses working on a wall with gloves" style="left:20px;top:330px;width:105px;height:140px"></div>
</section>

</body>
</html>
```